Business card design for holistic health care clinic

We need a double-sided business card design for our holistic health care clinic that integrates our logo design and also its color scheme. My business is called Valmira. It is an integrative medicine clinic. You have already done the logo for me. Please ensure an elegant and upscale design that is not cluttered, but still has all the necessary information (please see below for details).

Target Market(s)

Wellness, fitness, rehabilitation for educated, well-traveled open-minded clients who are focused on natural, organic, balanced and preventive healthcare and lifestyle.

Industry/Entity Type

Medical

Contact Information for Business Card

Modern, clean.

Number of Pages Required

1 page

Font styles to use
Serif
Sans Serif

Colors

Designer to choose colors to be used in the design.

Requirements
Must have
• Logo on one side, all other information on the other side.
• Other information should include:
• Tobias Wrenfeld - DOE, CPT, LMT
• 4100 East Marrow Drive
• Austin, TX 78119
• 512 555 0148
• 818 555 0192
• info@ValmiraHealth.example
• t.wrenfeld@ValmiraHealth.example
Nice to have
• Darker background on front - but not totally black - shaded/dark gray.

```html
<!DOCTYPE html>
<html lang="en">
<head>
<meta charset="utf-8">
<title>Valmira Business Card</title>
<link href="https://fonts.googleapis.com/css2?family=Nunito:wght@400;600;800&display=swap" rel="stylesheet">
<style>
  :root {
    --page-bg: #3a3330;
    --card-bg: #1d1e20;
    --brand-blue: #1a98d5;
    --text-font: "Nunito", Arial, sans-serif;
  }
  * { margin: 0; padding: 0; box-sizing: border-box; }
  html, body {
    width: 1200px; height: 780px; overflow: hidden;
    background: var(--page-bg);
    font-family: var(--text-font);
  }
  .canvas {
    position: relative; width: 1200px; height: 780px;
    display: flex; flex-direction: column; align-items: center; justify-content: center; gap: 40px;
  }
  .card {
    width: 580px; height: 330px;
    background: var(--card-bg);
    border-radius: 4px;
    box-shadow: 0 12px 30px rgba(0,0,0,0.45);
    color: var(--brand-blue);
    position: relative;
  }
  .card-front {
    display: flex; align-items: center; justify-content: center;
  }
  .brand { display: flex; flex-direction: column; align-items: flex-start; }
  .brand-row { display: flex; align-items: center; gap: 10px; }
  .brand-dot { width: 14px; height: 14px; border-radius: 50%; background: var(--brand-blue); }
  .brand-name {
    font-weight: 800; font-size: 58px; letter-spacing: 1px; line-height: 1;
    text-transform: uppercase;
  }
  .brand-tagline { font-weight: 600; font-size: 15px; margin-top: 6px; letter-spacing: 0.3px; }
  .card-back { display: flex; align-items: center; padding: 0 34px; }
  .card-back .brand-name { font-size: 46px; }
  .card-back .brand-tagline { font-size: 13px; }
  .divider { width: 1.5px; height: 190px; background: var(--brand-blue); margin: 0 28px; }
  .contact { display: flex; flex-direction: column; }
  .person-name { font-weight: 800; font-size: 17px; text-transform: uppercase; letter-spacing: 0.5px; }
  .person-credentials { font-weight: 400; font-size: 13px; margin-bottom: 14px; }
  .contact-line { display: flex; align-items: center; gap: 9px; font-size: 13px; margin-bottom: 5px; }
  .contact-icon { width: 16px; height: 16px; flex: none; }
  .address { font-size: 13px; margin-top: 8px; line-height: 1.35; }
</style>
</head>
<body>
<main class="canvas">
  <section class="card card-front">
    <div class="brand">
      <div class="brand-row">
        <span class="brand-dot"></span>
        <span class="brand-name">Valmira</span>
      </div>
      <span class="brand-tagline">Integrative Holistic Medicine</span>
    </div>
  </section>

  <section class="card card-back">
    <div class="brand">
      <div class="brand-row">
        <span class="brand-dot"></span>
        <span class="brand-name">Valmira</span>
      </div>
      <span class="brand-tagline">Integrative Holistic Medicine</span>
    </div>
    <div class="divider"></div>
    <div class="contact">
      <span class="person-name">Tobias Wrenfeld</span>
      <span class="person-credentials">DOE, CPT, LMT</span>
      <div class="contact-line">
        <svg class="contact-icon" viewBox="0 0 16 16"><circle cx="8" cy="8" r="7.2" fill="none" stroke="#1a98d5" stroke-width="1.2"/><rect x="5.5" y="3.8" width="5" height="8.4" rx="1" fill="none" stroke="#1a98d5" stroke-width="1.1"/></svg>
        <span>512 555 0148</span>
      </div>
      <div class="contact-line">
        <svg class="contact-icon" viewBox="0 0 16 16"><circle cx="8" cy="8" r="7.2" fill="none" stroke="#1a98d5" stroke-width="1.2"/><path d="M5.3 4.5l1.6-.4.8 1.9-1 .7a5 5 0 0 0 2.6 2.6l.7-1 1.9.8-.4 1.6c-3.4.4-6.6-2.8-6.2-6.2z" fill="#1a98d5"/></svg>
        <span>818 555 0192</span>
      </div>
      <div class="contact-line">
        <svg class="contact-icon" viewBox="0 0 16 16"><circle cx="8" cy="8" r="7.2" fill="none" stroke="#1a98d5" stroke-width="1.2"/><rect x="4.3" y="5.3" width="7.4" height="5.4" fill="none" stroke="#1a98d5" stroke-width="1.1"/><path d="M4.3 5.3L8 8.4l3.7-3.1" fill="none" stroke="#1a98d5" stroke-width="1.1"/></svg>
        <span>info@ValmiraHealth.example</span>
      </div>
      <div class="contact-line">
        <svg class="contact-icon" viewBox="0 0 16 16"><circle cx="8" cy="8" r="7.2" fill="none" stroke="#1a98d5" stroke-width="1.2"/><rect x="4.3" y="5.3" width="7.4" height="5.4" fill="none" stroke="#1a98d5" stroke-width="1.1"/><path d="M4.3 5.3L8 8.4l3.7-3.1" fill="none" stroke="#1a98d5" stroke-width="1.1"/></svg>
        <span>t.wrenfeld@ValmiraHealth.example</span>
      </div>
      <div class="address">4100 East Marrow Drive<br>Austin, TX 78119</div>
    </div>
  </section>
</main>
</body>
</html>
```